BRIGHT RIVER POWER.

I'd like my business logo.
contact name: Dennis Halvorsen
phone:0438759164
email: info@brightriverpower.net.au
website: www.brightriverpower.net.au

services:
solar
battery storage
LED lighting
energy saving solutions
general electrical
I'd like the design to look professional

Target Market(s)

Everyone

Industry/Entity Type

Business

Contact Information for Business Card

as described above

Requirements
Must have
• Id like the colours and the design to work well with my logo.

```html
<!DOCTYPE html>
<html lang="en">
<head>
<meta charset="utf-8">
<title>Bright River Power – Business Cards</title>
<link href="https://fonts.googleapis.com/css2?family=Open+Sans:wght@400;600;700&display=swap" rel="stylesheet">
<style>
  :root {
    --backdrop: #ece8e2;
    --card-black: #0c0c0c;
    --leaf-green: #7cc242;
    --sun-orange: #f7b52c;
    --text-white: #f2f2f2;
    --card-shadow: rgba(0, 0, 0, 0.35);
  }
  * { margin: 0; padding: 0; box-sizing: border-box; }
  html, body { width: 1200px; height: 900px; overflow: hidden; }
  body {
    background: var(--backdrop);
    font-family: "Open Sans", Arial, sans-serif;
    position: relative;
  }
  .card {
    position: absolute;
    width: 540px;
    height: 310px;
    background: var(--card-black);
    border-radius: 4px;
    box-shadow: 0 14px 30px var(--card-shadow);
    overflow: hidden;
    color: var(--text-white);
  }

  /* Services card */
  .card--services { left: 110px; top: 150px; }
  .brand-lockup {
    position: absolute;
    left: 0; right: 0; top: 62px;
    display: flex; align-items: center; justify-content: center; gap: 14px;
  }
  .brand-dot {
    width: 46px; height: 46px; border-radius: 50%;
    background: var(--leaf-green);
  }
  .brand-name {
    font-weight: 700;
    font-size: 34px;
    color: var(--leaf-green);
    letter-spacing: 0.5px;
  }
  .services-heading {
    position: absolute; left: 70px; top: 178px;
    font-size: 20px; font-weight: 600;
    color: var(--leaf-green);
    letter-spacing: 0.5px;
  }
  .service-list {
    position: absolute; list-style: none;
    font-size: 14px; line-height: 20px;
  }
  .service-list--left { left: 72px; top: 218px; }
  .service-list--right { left: 300px; top: 172px; }
  .service-list li::before {
    content: ""; display: inline-block;
    width: 6px; height: 6px; border-radius: 50%;
    background: var(--sun-orange);
    margin-right: 8px; vertical-align: middle;
  }

  /* Contact card */
  .card--contact { left: 520px; top: 410px; }
  .contact-wave { position: absolute; left: 0; top: 0; width: 540px; height: 310px; }
  .contact-mark {
    position: absolute; right: 78px; top: 36px;
    width: 90px; height: 90px; border-radius: 50%;
    background: var(--leaf-green);
  }
  .contact-name {
    position: absolute; left: 58px; top: 78px;
    font-size: 21px; font-weight: 700;
    color: var(--sun-orange);
  }
  .contact-list {
    position: absolute; left: 60px; top: 140px;
    list-style: none; font-size: 15px; line-height: 22px;
  }
  .contact-list li { display: flex; align-items: center; gap: 9px; }
  .contact-icon { width: 12px; height: 12px; fill: var(--sun-orange); }
</style>
</head>
<body>

  <section class="card card--services">
    <div class="brand-lockup">
      <span class="brand-dot"></span>
      <span class="brand-name">BRIGHT RIVER POWER</span>
    </div>
    <h2 class="services-heading">WHAT I DO</h2>
    <ul class="service-list service-list--left">
      <li>Solar</li>
      <li>Battery Storage</li>
    </ul>
    <ul class="service-list service-list--right">
      <li>LED Lighting</li>
      <li>Energy Saving Solutions</li>
    </ul>
  </section>

  <section class="card card--contact">
    <svg class="contact-wave" viewBox="0 0 540 310" aria-hidden="true">
      <path d="M0,250 C220,252 400,222 500,152 C390,238 200,268 0,272 Z" fill="var(--sun-orange)"/>
      <path d="M0,268 C220,268 420,236 540,140 L540,310 L0,310 Z" fill="var(--leaf-green)"/>
    </svg>
    <span class="contact-mark"></span>
    <h1 class="contact-name">Dennis Halvorsen</h1>
    <ul class="contact-list">
      <li>
        <svg class="contact-icon" viewBox="0 0 12 12"><path d="M2.5 0.5 L4.5 0.5 L5.5 3.5 L4 4.5 C4.7 6 6 7.3 7.5 8 L8.5 6.5 L11.5 7.5 L11.5 9.5 C11.5 10.6 10.6 11.5 9.5 11.5 C4.5 11.5 0.5 7.5 0.5 2.5 C0.5 1.4 1.4 0.5 2.5 0.5 Z"/></svg>
        <span>0438759164</span>
      </li>
      <li>
        <svg class="contact-icon" viewBox="0 0 12 12"><path d="M0.5 2.5 H11.5 V10 H0.5 Z M1 3 L6 7 L11 3" stroke="#0c0c0c" stroke-width="0.8"/></svg>
        <span>info@brightriverpower.net.au</span>
      </li>
      <li>
        <svg class="contact-icon" viewBox="0 0 12 12"><path d="M4.5 7.5 L7.5 4.5" stroke="var(--sun-orange)" stroke-width="1.4" fill="none"/><circle cx="3" cy="9" r="2.2" fill="none" stroke="var(--sun-orange)" stroke-width="1.3"/><circle cx="9" cy="3" r="2.2" fill="none" stroke="var(--sun-orange)" stroke-width="1.3"/></svg>
        <span>www.brightriverpower.net.au</span>
      </li>
    </ul>
  </section>

</body>
</html>
```